Business Card Design

We are a commercial real estate brokerage in San Francisco, leasing office buildings downtown.
I would like a clean, elegant look. Simple but powerful .

Industry/Entity Type

Business

Contact Information for Business Card

Derek Holloway
lic# 07258143
415.555.0172
derek@velt-commercial.example
velt-commercial.example

```html
<!DOCTYPE html>
<html lang="en">
<head>
<meta charset="utf-8">
<title>VELT Commercial — Business Card</title>
<link rel="stylesheet" href="https://fonts.googleapis.com/css2?family=Arimo:wght@400&display=swap">
<style>
  :root {
    --backdrop: #4a403a;
    --card: #1c1c1e;
    --card-edge: #2a2a2c;
    --accent: #8d9dbd;
    --ink: #e6e6e6;
    --muted: #6f6f73;
    --mark: #3a3a3d;
  }
  * { box-sizing: border-box; margin: 0; padding: 0; }
  html, body {
    width: 1200px; height: 787px; overflow: hidden;
    background: var(--backdrop);
    font-family: "Arimo", Arial, sans-serif;
  }
  .stage {
    position: relative; width: 1200px; height: 787px;
    display: flex; align-items: center; justify-content: center; gap: 60px;
  }
  .card {
    position: relative; width: 510px; height: 292px;
    background: var(--card);
    border: 1px solid var(--card-edge);
    box-shadow: 0 8px 24px rgba(0,0,0,.35);
  }
  .brand {
    position: absolute; display: flex; align-items: center; gap: 12px;
  }
  .brand-square {
    width: 16px; height: 16px; background: var(--mark);
  }
  .brand-name {
    font-size: 34px; letter-spacing: 2px; line-height: 1;
    color: var(--mark);
  }
  .card-back .brand { left: 72px; top: 70px; }
  .card-back .tagline {
    position: absolute; left: 72px; top: 150px; width: 370px;
    font-size: 15px; line-height: 1.55; color: var(--ink);
  }
  .card-front .brand { left: 150px; top: 82px; }
  .card-front .brand-name { color: var(--accent); }
  .card-front .brand-square { background: var(--accent); }
  .agent {
    position: absolute; left: 48px; top: 168px;
  }
  .agent-name { font-size: 19px; color: var(--accent); }
  .agent-licence { margin-top: 8px; font-size: 16px; color: var(--ink); padding-left: 10px; }
  .contacts {
    position: absolute; left: 238px; top: 176px; list-style: none;
  }
  .contacts li {
    display: flex; align-items: center; gap: 8px;
    font-size: 16px; color: var(--ink); margin-bottom: 7px;
  }
  .contacts svg { width: 14px; height: 14px; fill: var(--ink); flex: none; }
</style>
</head>
<body>
<main class="stage">
  <section class="card card-back" aria-label="Card back">
    <div class="brand">
      <span class="brand-square"></span>
      <span class="brand-name">VELT COMMERCIAL</span>
    </div>
    <p class="tagline">commercial real estate brokerage in San Francisco leasing office buildings downtown.</p>
  </section>

  <section class="card card-front" aria-label="Card front">
    <div class="brand">
      <span class="brand-square"></span>
      <span class="brand-name">VELT COMMERCIAL</span>
    </div>
    <div class="agent">
      <p class="agent-name">Derek Holloway</p>
      <p class="agent-licence">lic# 07258143</p>
    </div>
    <ul class="contacts">
      <li>
        <svg viewBox="0 0 16 16" aria-hidden="true"><path d="M2 5c0-2 2-3 6-3s6 1 6 3v1h-3V5H5v1H2z"/><rect x="3" y="7" width="10" height="7" rx="1"/></svg>
        415.555.0172
      </li>
      <li>
        <svg viewBox="0 0 16 16" aria-hidden="true"><path d="M1 3h14v10H1z M1 3l7 6 7-6" fill="none" stroke="#e6e6e6" stroke-width="1.6"/></svg>
        derek@velt-commercial.example
      </li>
      <li>
        <svg viewBox="0 0 16 16" aria-hidden="true"><circle cx="8" cy="8" r="7"/><circle cx="8" cy="7" r="2.2" fill="#1c1c1e"/></svg>
        velt-commercial.example
      </li>
    </ul>
  </section>
</main>
</body>
</html>
```